institute for female grief councelors needs a design for its facebook group

Each year about 350.000 German women do have a misscarriage while they are pregnant. Their pain and grief is soul deep. Lots of them are stay still in grief even if they have got other children who are healthy and alive. Lots of these women have got difficulty in finally letting go pain, rage and grief. Some are even still in grief after more than twenty or thirty years of having lost their child through misscarriage!!!!

With this facebook group I want to give hope, trust and support as well as helpful advice in coping with this deep soul pain after having lost your child through misscarriage.

The facebook cover shall cause a great curiosity and fascination to the mothers so that they are interested in joining our facebook group.

At our institute women can book a-one-year-training to become a certified "Coach for BirkenFeen" (grief councelor for women who are in deep grief after their misscarriage).

In Germany children who died through misscarriage are named "Sternenkind" (STARCHILD).
Therefore I want to have at least one shing star at the facebook cover symbolizing the still shining soullight of the dead child watching its mother who is still living on earth.

On the left side of the uploaded file you see the planet venus: symbol for mothers / female side of life.
The red sky colour symbolizes the colour of the uterus, the embryo's home before having died through misscarriage.
It ist also possible to include the silhoutte of a mother / several mothers looking up into the red / blue sky to watch the shining soullight of their dead child.

The facebook cover MUST include the following sentence:

Mama, ich lasse mein Licht für dich leuchten

(Mummy, I let my soullight shine for you)

Low design quality

Target Market(s)

German speaking mothers

Industry/Entity Type

coaching

Font styles to use
Script

Colors

Designer to choose colors to be used in the design.

Requirements
Must have
• golden fond writing, at least one shing star, silhouette of one / several mothers (no model typa - normal woman)
Nice to have
• planet venus - red background cover (like uterus colour)
Should not have
• mothers who like like a model or filmstar

```html
<!DOCTYPE html>
<html lang="de">
<head>
<meta charset="utf-8">
<title>Sternenkind – Facebook Cover</title>
<link rel="stylesheet" href="https://fonts.googleapis.com/css2?family=Pacifico&family=Poppins:wght@600&display=swap">
<style>
  :root {
    --space-deep: #120c24;
    --space-violet: #3a1d4a;
    --nebula-red: #a8403a;
    --nebula-orange: #d9734a;
    --glow: #fff3e0;
    --venus-light: #f3d596;
    --venus-mid: #d9ae68;
    --venus-edge: #b98a4a;
    --silhouette: #050305;
    --gold: #e2b446;
    --gold-deep: #a97a22;
    --flag-black: #000000;
    --flag-red: #ff0000;
    --flag-gold: #ffff00;
    --button-bg: #ffffff;
  }
  * { margin: 0; padding: 0; box-sizing: border-box; }
  html, body { width: 1200px; height: 676px; overflow: hidden; background: var(--space-deep); }
  .cover { position: relative; width: 1200px; height: 676px; overflow: hidden; }

  .night-sky {
    position: absolute; inset: 0;
    background:
      radial-gradient(circle at 1003px 125px, var(--glow) 0, rgba(255,220,190,.8) 40px, rgba(217,115,74,.45) 120px, transparent 300px),
      radial-gradient(ellipse 520px 360px at 1000px 160px, rgba(168,64,58,.75), transparent 70%),
      radial-gradient(ellipse 500px 400px at 700px 120px, rgba(90,40,90,.6), transparent 70%),
      linear-gradient(160deg, var(--space-deep) 0%, var(--space-violet) 55%, #2a1230 100%);
  }

  .flag-bar { position: absolute; left: 0; top: 0; width: 12px; height: 608px; display: flex; flex-direction: column; }
  .flag-bar span:nth-child(1) { height: 240px; background: var(--flag-black); }
  .flag-bar span:nth-child(2) { height: 178px; background: var(--flag-red); }
  .flag-bar span:nth-child(3) { height: 190px; background: var(--flag-gold); }

  .venus {
    position: absolute; left: 84px; top: 130px; width: 526px; height: 526px; border-radius: 50%;
    background: radial-gradient(circle at 45% 40%, var(--venus-light) 0%, var(--venus-mid) 65%, var(--venus-edge) 100%);
  }

  .mother-silhouette {
    position: absolute; left: 234px; top: 313px; width: 385px; height: 363px;
    background: var(--silhouette);
    border-radius: 50% 50% 0 0 / 40% 40% 0 0;
  }

  .sparkle { position: absolute; left: 1066px; top: 30px; width: 110px; height: 90px; }

  .message {
    position: absolute; left: 660px; top: 205px; width: 494px;
    font-family: "Pacifico", cursive; font-size: 58px; line-height: 92px;
    text-align: center; color: transparent;
    -webkit-text-stroke: 1.6px var(--gold);
    text-shadow: 0 0 6px rgba(226,180,70,.35);
  }

  .join { position: absolute; left: 815px; top: 585px; display: flex; align-items: center; gap: 10px; }
  .join-heart { width: 40px; height: 36px; }
  .join-button {
    height: 44px; padding: 0 14px; border-radius: 8px; background: var(--button-bg);
    font-family: "Poppins", sans-serif; font-weight: 600; font-size: 25px; line-height: 44px;
    color: var(--gold-deep); letter-spacing: .5px;
  }
</style>
</head>
<body>
  <main class="cover">
    <div class="night-sky" role="img" aria-label="Sternenhimmel mit rötlichem Nebel und einem hell leuchtenden Stern"></div>
    <div class="flag-bar" aria-hidden="true"><span></span><span></span><span></span></div>
    <div class="venus" role="img" aria-label="Planet Venus in warmem Goldgelb"></div>
    <div class="mother-silhouette" role="img" aria-label="Silhouette einer Mutter mit wehendem Haar, die nach oben blickt"></div>

    <svg class="sparkle" viewBox="0 0 110 90" aria-hidden="true">
      <path d="M40 0 L45 38 L80 45 L45 52 L40 90 L35 52 L0 45 L35 38 Z" fill="#fff4d8"/>
      <path d="M88 8 L90 18 L100 20 L90 22 L88 32 L86 22 L76 20 L86 18 Z" fill="#ffe3b0"/>
      <path d="M92 50 L94 62 L106 64 L94 66 L92 78 L90 66 L78 64 L90 62 Z" fill="#ffd79a"/>
    </svg>

    <h1 class="message">Mama,<br>ich lasse mein<br>Licht für dich<br>leuchten</h1>

    <div class="join">
      <svg class="join-heart" viewBox="0 0 40 36" aria-hidden="true">
        <path d="M20 35 C6 24 0 17 0 10 C0 4 5 0 10 0 C14 0 18 2 20 6 C22 2 26 0 30 0 C35 0 40 4 40 10 C40 17 34 24 20 35 Z" fill="var(--gold)"/>
      </svg>
      <span class="join-button">JOIN NOW</span>
    </div>
  </main>
</body>
</html>
```